Create a highly polished design and structured Sales Agreement template

We need a professionally designed Sales Agreement template for our company, Harrowgate Labs, Inc. This template will be used to formalize agreements with our customers for calibration services. The design should reflect the high standards and professionalism of a Keystone 250 company.
Key requirements:
Incorporate our company logo and branding elements.
Ensure the template includes sections for all critical details such as customer name, address, services provided, pricing, and terms of payment.
The layout should be clean, modern, and easy to navigate.
Include placeholders for variable information (e.g., customer name, address, etc.) that can be easily filled out for each customer.
Design the template in a way that allows our team to update it easily via a form entry system.
Ensure the language and formatting are polished and professional.
We have attached our current Sales Agreement for reference. Please maintain all key details while enhancing the structure, format, and overall presentation.

```html
<!DOCTYPE html>
<html lang="en">
<head>
<meta charset="utf-8">
<title>Harrowgate Labs – Facilities Management Service Proposal</title>
<link href="https://fonts.googleapis.com/css2?family=Bebas+Neue&family=Montserrat:wght@400;500;600;700&display=swap" rel="stylesheet">
<style>
:root{
  --teal:#17968a;
  --teal-dark:#0d6e66;
  --ink:#111111;
  --text:#2b2b2b;
  --grey:#c6c6c6;
  --bg:#3a3a3c;
  --paper:#ffffff;
}
*{box-sizing:border-box;margin:0;padding:0}
html,body{width:1200px;height:1076px;overflow:hidden;background:var(--bg)}
body{position:relative;font-family:"Montserrat",sans-serif;color:var(--text)}
.page{position:absolute;width:313px;height:443px;background:var(--paper);overflow:hidden}
.p-cover{left:100px;top:70px}
.p-toc{left:441px;top:70px}
.p-sales{left:787px;top:70px}
.p-chart{left:100px;top:547px}
.p-columns{left:441px;top:547px}
.p-gallery{left:787px;top:547px}
.abs{position:absolute}

/* cover */
.cover-bg{position:absolute;inset:0;background:linear-gradient(180deg,#000 0%,#05231f 14%,#0f6f66 38%,#149085 62%,#17968a 100%)}
.cover-photo{position:absolute;left:0;top:80px;width:313px;height:250px;background:linear-gradient(180deg,rgba(20,140,128,.0),rgba(160,210,200,.25) 50%,rgba(20,140,128,0));}
.cover-tab{position:absolute;left:105px;top:-10px;width:103px;height:112px;background:var(--paper);border:6px solid var(--grey);border-top:none;border-radius:0 0 52px 52px;display:flex;flex-direction:column;align-items:center;justify-content:center;padding-top:12px;gap:5px}
.cover-tab .mark{width:30px;height:30px;border-radius:50%;background:#b9b9b9}
.cover-tab .name{font-weight:700;color:var(--teal);font-size:7.5px;text-align:center;line-height:1.1}
.cover-title{position:absolute;left:0;width:313px;top:128px;text-align:center;font-family:"Bebas Neue",sans-serif;color:#fff;font-size:49px;line-height:41px}
.cover-sub{position:absolute;left:0;width:313px;top:340px;text-align:center;font-weight:700;font-size:19px;line-height:19px}
.cover-sub .k{color:var(--ink)}
.cover-sub .w{color:#fff}
.cover-url{position:absolute;left:0;width:313px;top:402px;text-align:center;color:#fff;font-size:6.3px;letter-spacing:.8px;font-weight:500}
.cover-rule{position:absolute;left:122px;top:416px;width:70px;height:1px;background:#fff}

/* shared inner page chrome */
.side-bar{position:absolute;left:17px;top:0;width:8px;height:53px;background:var(--teal);border-radius:0 0 4px 4px}
.page-title{position:absolute;left:29px;top:26px;font-weight:700;line-height:1}
.page-title .l1{display:block;color:var(--ink);font-size:11.5px}
.page-title .l2{display:block;color:var(--teal);font-size:16px;margin-top:1px}
.brand-tab{position:absolute;left:248px;top:-3px;width:48px;height:56px;background:var(--paper);border:3px solid var(--grey);border-top:none;border-radius:0 0 24px 24px;display:flex;flex-direction:column;align-items:center;justify-content:center;gap:2px;padding-top:4px}
.brand-tab .mark{width:14px;height:14px;border-radius:50%;background:#bdbdbd}
.brand-tab .name{font-weight:700;color:var(--teal);font-size:3.6px;text-align:center;line-height:1.1}
.footer{position:absolute;left:17px;top:421px;width:279px;border-top:1px solid var(--teal);height:12px}
.footer .label{position:absolute;left:0;top:3px;font-size:5.4px;font-weight:600;color:var(--ink)}
.footer .num{position:absolute;right:0;top:1px;background:var(--teal);color:#fff;font-size:5px;font-weight:700;padding:2px 6px}

/* toc */
.toc{position:absolute;left:21px;top:87px;width:272px;list-style:none}
.toc li{position:relative;height:9px;margin-bottom:4.4px;background:var(--ink);border-radius:5px;color:#fff;font-size:5.2px;line-height:9px}
.toc .n{position:absolute;left:6px;width:10px}
.toc .bar{position:absolute;left:20px;right:17px;top:0;bottom:0;background:var(--teal);border-radius:0 5px 5px 0;padding-left:6px}
.toc .pg{position:absolute;right:5px}

/* sales agreement */
.sa{position:absolute;left:17px;width:282px;font-size:4.5px;line-height:7.6px;color:var(--text)}
.sa-h{position:absolute;left:17px;color:var(--teal);font-weight:600;font-size:7.6px}
.sa-h.small{font-size:4.6px}
.sa b{font-weight:700;color:var(--ink)}
.sa .num{color:var(--teal);font-weight:700}

/* body copy */
.h-teal{position:absolute;color:var(--teal);font-weight:600;font-size:10px}
.h-ink{position:absolute;color:var(--ink);font-weight:600;font-size:10px}
.copy{position:absolute;font-size:4.6px;line-height:7.65px;text-align:justify;overflow:hidden;color:var(--text)}
.sub-h{position:absolute;left:17px;color:var(--ink);font-weight:600;font-size:8px}
.list{position:absolute;left:36px;font-size:4.7px;line-height:8.6px;list-style:none}
.chart{position:absolute;left:252px}
.data-table{position:absolute;left:16px;top:323px;width:281px;border-collapse:collapse;font-size:4.2px}
.data-table th{background:#c9c9c9;color:#fff;font-weight:500;height:14px;text-align:center;line-height:1.1}
.data-table th:first-child{text-align:left;padding-left:3px}
.data-table td{height:12.7px;border-bottom:1px solid #d5d5d5;text-align:center;color:var(--text)}
.data-table td:first-child{text-align:left;padding-left:3px;width:86px}
.data-table th.hl{background:var(--teal)}
.data-table .hl{border-left:1px solid var(--teal);border-right:1px solid var(--teal)}
.data-table tr:last-child .hl{border-bottom:1px solid var(--teal)}
.photo{position:absolute}
</style>
</head>
<body>

<!-- Cover -->
<section class="page p-cover">
  <div class="cover-bg"></div>
  <div class="cover-photo" role="img" aria-label="Photo of a facility interior with rows of equipment, tinted teal"></div>
  <div class="cover-tab"><span class="mark"></span><span class="name">HARROWGATE<br>LABS</span></div>
  <h1 class="cover-title">Facilities<br>Management<br>Service</h1>
  <div class="cover-sub"><span class="k">COMPANY</span><br><span class="w">PROPOSAL</span><br><span class="w">2024</span></div>
  <div class="cover-url">www.harrowgatelabs.com</div>
  <div class="cover-rule"></div>
</section>

<!-- Table of contents -->
<section class="page p-toc">
  <div class="side-bar"></div>
  <h2 class="page-title"><span class="l1">TABLE OF</span><span class="l2">CONTENTS</span></h2>
  <div class="brand-tab"><span class="mark"></span><span class="name">HARROWGATE<br>LABS</span></div>
  <ol class="toc">
    <li><span class="n">1</span><span class="bar">Heading Goes Here</span><span class="pg">1</span></li>
    <li><span class="n">2</span><span class="bar">Heading Goes Here</span><span class="pg">2</span></li>
    <li><span class="n">3</span><span class="bar">Heading Goes Here</span><span class="pg">3</span></li>
    <li><span class="n">4</span><span class="bar">Heading Goes Here</span><span class="pg">4</span></li>
    <li><span class="n">5</span><span class="bar">Heading Goes Here</span><span class="pg">5</span></li>
    <li><span class="n">6</span><span class="bar">Heading Goes Here</span><span class="pg">6</span></li>
    <li><span class="n">7</span><span class="bar">Heading Goes Here</span><span class="pg">7</span></li>
    <li><span class="n">8</span><span class="bar">Heading Goes Here</span><span class="pg">8</span></li>
    <li><span class="n">9</span><span class="bar">Heading Goes Here</span><span class="pg">9</span></li>
    <li><span class="n">10</span><span class="bar">Heading Goes Here</span><span class="pg">10</span></li>
    <li><span class="n">11</span><span class="bar">Heading Goes Here</span><span class="pg">11</span></li>
    <li><span class="n">12</span><span class="bar">Heading Goes Here</span><span class="pg">12</span></li>
    <li><span class="n">13</span><span class="bar">Heading Goes Here</span><span class="pg">13</span></li>
    <li><span class="n">14</span><span class="bar">Heading Goes Here</span><span class="pg">14</span></li>
    <li><span class="n">15</span><span class="bar">Heading Goes Here</span><span class="pg">15</span></li>
    <li><span class="n">16</span><span class="bar">Heading Goes Here</span><span class="pg">16</span></li>
    <li><span class="n">17</span><span class="bar">Heading Goes Here</span><span class="pg">17</span></li>
    <li><span class="n">18</span><span class="bar">Heading Goes Here</span><span class="pg">18</span></li>
    <li><span class="n">19</span><span class="bar">Heading Goes Here</span><span class="pg">19</span></li>
    <li><span class="n">20</span><span class="bar">Heading Goes Here</span><span class="pg">20</span></li>
  </ol>
  <div class="footer"><span class="label">FACILITIES MANAGEMENT SERVICE</span><span class="num">PAGE - 01</span></div>
</section>

<!-- Sales agreement -->
<section class="page p-sales">
  <div class="side-bar"></div>
  <h2 class="page-title" style="top:29px"><span class="l1">SALES</span><span class="l2">AGREEMENT</span></h2>
  <div class="brand-tab"><span class="mark"></span><span class="name">HARROWGATE<br>LABS</span></div>

  <div class="sa-h" style="top:72px">Seller:</div>
  <p class="sa" style="top:83px">Harrowgate Labs, Inc. 4120 N Ridgeline Ave, Suite B Meridian, ID 83646 Phone: 800-555-0148</p>
  <div class="sa-h" style="top:96px">Customer:</div>
  <p class="sa" style="top:107px">[Customer Name] [Customer Address] [Customer City, State, Zip] Phone: [Customer Phone] Email: [Customer Email]</p>

  <div class="sa-h" style="top:125px">SERVICES</div>
  <p class="sa" style="top:136px">Harrowgate Labs, Inc. agrees to provide the following services to [Customer Name]:</p>
  <p class="sa" style="top:145px"><span class="num">1.</span> Calibration Services: Full-time on-site trained technician support.</p>
  <p class="sa" style="top:153px"><span class="num">2.</span> Turn-key Service Management: Scheduling, on-site calibrations, pick-up and delivery, turn time management, and<br>&nbsp;&nbsp;&nbsp;interface with selected vendors.</p>
  <p class="sa" style="top:168px"><span class="num">3.</span> Document Control: Online access to calibration documents via our website.</p>

  <div class="sa-h" style="top:185px">PRICING</div>
  <p class="sa" style="top:194px"><b>Dedicated On-site Technician (3 Days per Week)</b></p>
  <p class="sa" style="top:204px">· Monthly Charge: $12,500.00<br>· Yearly Total: $150,000.00<br>· Sales tax not included.<br>· Potential annual price increase of 3% beginning the second year.</p>

  <div class="sa-h small" style="top:258px">SIGNATURES</div>
  <p class="sa" style="top:265px"><b>Harrowgate Labs, Inc.:</b></p>
  <p class="sa" style="top:305px">[Authorized Signatory Name]<br>[Title]<br>Date: _______________<br>[Customer Name]:</p>
  <p class="sa" style="top:345px">[Authorized Signatory Name]<br>[Title]<br>Date: _______________</p>
  <div class="footer"><span class="label">FACILITIES MANAGEMENT SERVICE</span><span class="num">PAGE - 01</span></div>
</section>

<!-- Content page with chart and table -->
<section class="page p-chart">
  <div class="side-bar"></div>
  <h2 class="page-title" style="top:29px"><span class="l1">HEADING</span><span class="l2">GOES HERE</span></h2>
  <div class="brand-tab"><span class="mark"></span><span class="name">HARROWGATE<br>LABS</span></div>

  <h3 class="h-teal" style="left:17px;top:70px">HEADING GOES HERE</h3>
  <p class="copy" style="left:17px;top:84px;width:279px;height:70px">Lorem ipsum dolor sit amet, consectetuer adipiscing elit, sed diam nonummy nibh euismod tincidunt ut laoreet dolore magna aliquam erat volutpat. Ut wisi enim ad minim veniam, quis nostrud exerci tation ullamcorper suscipit lobortis nisl ut aliquip ex ea tation ullamcorper suscipit lobortis nisl ut aliquip ex ea commodo consequat. Duis autem vel eum iriure dolor in hendrerit in vulputate velit esse molestie consequat, vel illum dolore eu feugiat nulla facilisis at vero eros et accumsan et iusto odio dignis Lorem ipsum dolor sit amet, consectetuer adipiscing elit, sed diam nonummy nibh euismod tincidunt ut laoreet dolore magna aliquam erat volutpat. Ut wisi enim ad minim veniam, quis nostrud exerci tation ullamcorper suscipit lobortis nisl ut aliquip ex ea tation ullamcorper suscipit lobortis nisl ut aliquip ex ea commodo consequat. Duis autem vel eum iriure dolor in hendrerit in vulputate velit esse molestie consequat, vel illum dolore eu feugiat nulla facilisis at vero eros et accumsan et iusto odio dignis</p>

  <h4 class="sub-h" style="top:159px">1.1. HEADING GOES HERE</h4>
  <ul class="list" style="top:167px"><li>a) Lorem ipsum dolor sit amet,</li><li>b)Lorem ipsum dolor sit amet,</li></ul>
  <h4 class="sub-h" style="top:196px">1.2. HEADING GOES HERE</h4>
  <ul class="list" style="top:208px"><li>a) Lorem ipsum dolor sit amet,</li><li>b) Lorem ipsum dolor sit amet,</li><li>c) Lorem ipsum dolor sit amet,</li><li>d) Lorem ipsum dolor sit amet,</li></ul>

  <svg class="chart" style="left:150px;top:161px" width="144" height="82" viewBox="0 0 144 82" font-family="Montserrat, sans-serif">
    <text x="76" y="7" text-anchor="middle" font-size="7.2" fill="#555" font-weight="500">Temperature in well 20 in °C</text>
    <g font-size="3.8" fill="#555" text-anchor="end">
      <text x="15" y="16">140</text><text x="15" y="23">120</text><text x="15" y="30">100</text><text x="15" y="37">80</text><text x="15" y="44">60</text><text x="15" y="51">40</text><text x="15" y="58">20</text><text x="15" y="65">0</text>
    </g>
    <g fill="#c4c4c4">
      <rect x="22" y="44.3" width="7" height="19.7"/>
      <rect x="35" y="49.2" width="7" height="14.8"/>
      <rect x="48" y="33.9" width="7" height="30.1"/>
      <rect x="61" y="32.5" width="7" height="31.5"/>
      <rect x="74" y="29.7" width="7" height="34.3"/>
      <rect x="87" y="23.8" width="7" height="40.2"/>
      <rect x="100" y="20.3" width="7" height="43.7"/>
      <rect x="113" y="19.6" width="7" height="44.4"/>
      <rect x="126" y="18.9" width="7" height="45.1"/>
    </g>
    <line x1="18" y1="64" x2="137" y2="64" stroke="#bbb" stroke-width=".5"/>
    <g font-size="3.8" fill="#555" text-anchor="middle">
      <text x="25.5" y="42">56</text><text x="38.5" y="47">42</text><text x="51.5" y="32">86</text><text x="64.5" y="30">90</text><text x="77.5" y="27.5">98</text><text x="90.5" y="21.5">115</text><text x="103.5" y="18">125</text><text x="116.5" y="17.5">127</text><text x="129.5" y="16.8">129</text>
      <text x="25.5" y="72">2000</text><text x="38.5" y="72">2002</text><text x="51.5" y="72">2003</text><text x="64.5" y="72">2004</text><text x="77.5" y="72">2005</text><text x="90.5" y="72">2006</text><text x="103.5" y="72">2007</text><text x="116.5" y="72">2008</text><text x="129.5" y="72">2009</text>
    </g>
  </svg>

  <h3 class="h-teal" style="left:17px;top:262px">HEADING GOES HERE</h3>
  <p class="copy" style="left:17px;top:275px;width:279px;height:39px">Lorem ipsum dolor sit amet, consectetuer adipiscing elit, sed diam nonummy nibh euismod tincidunt ut laoreet dolore magna aliquam erat volutpat. Ut wisi enim ad minim veniam, quis nostrud exerci tation ullamcorper suscipit lobortis nisl ut aliquip ex ea tation ullamcorper suscipit lobortis nisl ut aliquip ex ea commodo consequat. Duis autem vel eum iriure dolor in hendrerit in vulputate velit esse molestie consequat, vel illum dolore eu feugiat nulla facilisis at vero eros et accumsan et iusto odio dignis Lorem ipsum dolor sit amet,</p>

  <table class="data-table">
    <tr><th>Heading Goes Here</th><th class="hl">Heading<br>Goes Here</th><th>Heading<br>Goes Here</th><th>Heading<br>Goes Here</th><th>Heading<br>Goes Here</th></tr>
    <tr><td>Lorem Ipsum Goes Here</td><td class="hl">23</td><td>12</td><td>78</td><td>12</td></tr>
    <tr><td>Lorem Ipsum Goes Here</td><td class="hl">45</td><td>56</td><td>12</td><td>56</td></tr>
    <tr><td>Lorem Ipsum Goes Here</td><td class="hl">78</td><td>76</td><td>34</td><td>76</td></tr>
    <tr><td>Lorem Ipsum Goes Here</td><td class="hl">22</td><td>12</td><td>55</td><td>12</td></tr>
  </table>
  <div class="footer"><span class="label">FACILITIES MANAGEMENT SERVICE</span><span class="num">PAGE - 01</span></div>
</section>

<!-- Two column content page -->
<section class="page p-columns">
  <div class="side-bar"></div>
  <h2 class="page-title" style="top:29px"><span class="l1">HEADING</span><span class="l2">GOES HERE</span></h2>
  <div class="brand-tab"><span class="mark"></span><span class="name">HARROWGATE<br>LABS</span></div>

  <h3 class="h-ink" style="left:17px;top:70px">HEADING GOES HERE</h3>
  <p class="copy" style="left:17px;top:84px;width:127px;height:154px">Lorem ipsum dolor sit amet, consectetuer adipiscing elit, sed diam nonummy nibh euismod tincidunt ut laoreet dolore magna aliquam erat volutpat. Ut wisi enim ad minim veniam, quis nostrud exerci tation ullamcorper suscipit lobortis nisl ut aliquip ex ea tation ullamcorper suscipit lobortis nisl ut aliquip ex ea commodo consequat. Duis autem vel eum iriure dolor in hendrerit in vulputate velit esse molestie consequat, vel illum dolore eu feugiat nulla facilisis at vero eros et accumsan et iusto odio dignis Lorem ipsum dolor sit amet, consectetuer adipiscing elit, sed diam nonummy nibh euismod tincidunt ut laoreet dolore magna aliquam erat volutpat. Ut wisi enim ad minim veniam, quis nostrud exerci tation ullamcorper suscipit lobortis nisl ut aliquip ex ea tation ullamcorper suscipit lobortis nisl ut aliquip ex ea commodo consequat. Duis autem vel eum iriure dolor in hendrerit in vulputate velit esse molestie consequat, vel illum dolore eu feugiat nulla facilisis at vero eros et accumsan</p>
  <div class="photo" role="img" aria-label="Photo of colleagues talking at a meeting table in a bright office" style="left:17px;top:241px;width:127px;height:86px;border:1.5px solid var(--teal);background:linear-gradient(135deg,#6f6f72 0%,#c9c4bd 45%,#e8e6e2 70%,#9aa0a6 100%)"></div>
  <p class="copy" style="left:17px;top:333px;width:127px;height:48px">Lorem ipsum dolor sit amet, consectetuer adipiscing elit, sed diam nonummy nibh euismod tincidunt ut laoreet dolore magna aliquam erat volutpat. Ut wisi enim ad minim veniam, quis nostrud exerci tation ullamcorper suscipit lobortis nisl ut aliquip ex ea commodo consequat. Duis autem vel eum iriure dolor in hendrerit in vulputate velit esse molestie</p>

  <h3 class="h-ink" style="left:168px;top:70px">HEADING GOES HERE</h3>
  <p class="copy" style="left:168px;top:84px;width:127px;height:154px">Lorem ipsum dolor sit amet, consectetuer adipiscing elit, sed diam nonummy nibh euismod tincidunt ut laoreet dolore magna aliquam erat volutpat. Ut wisi enim ad minim veniam, quis nostrud exerci tation ullamcorper suscipit lobortis nisl ut aliquip ex ea tation ullamcorper suscipit lobortis nisl ut aliquip ex ea commodo consequat. Duis autem vel eum iriure dolor in hendrerit in vulputate velit esse molestie consequat, vel illum dolore eu feugiat nulla facilisis at vero eros et accumsan et iusto odio dignis Lorem ipsum dolor sit amet, consectetuer adipiscing elit, sed diam nonummy nibh euismod tincidunt ut laoreet dolore magna aliquam erat volutpat. Ut wisi enim ad minim veniam, quis nostrud exerci tation ullamcorper suscipit lobortis nisl ut aliquip ex ea tation ullamcorper suscipit lobortis nisl ut aliquip ex ea commodo consequat. Duis autem vel eum iriure dolor in hendrerit in vulputate velit esse molestie consequat, vel illum dolore eu feugiat nulla facilisis at vero eros et accumsan</p>
  <h3 class="h-ink" style="left:168px;top:247px">HEADING GOES HERE</h3>
  <p class="copy" style="left:168px;top:261px;width:127px;height:120px">Lorem ipsum dolor sit amet, consectetuer adipiscing elit, sed diam nonummy nibh euismod tincidunt ut laoreet dolore magna aliquam erat volutpat. Ut wisi enim ad minim veniam, quis nostrud exerci tation ullamcorper suscipit lobortis nisl ut aliquip ex ea tation ullamcorper suscipit lobortis nisl ut aliquip ex ea commodo consequat. Duis autem vel eum iriure dolor in hendrerit in vulputate velit esse molestie consequat, vel illum dolore eu feugiat nulla facilisis at vero eros et accumsan et iusto odio dignis Lorem ipsum dolor sit amet, consectetuer adipiscing elit, sed diam nonummy nibh euismod tincidunt ut laoreet dolore magna aliquam erat volutpat. Ut wisi enim ad minim veniam, quis nostrud exerci tation ullamcorper suscipit lobortis nisl ut aliquip ex ea tation ullamcorper suscipit lobortis nisl ut aliquip ex</p>
  <div class="footer"><span class="label">FACILITIES MANAGEMENT SERVICE</span><span class="num">PAGE - 01</span></div>
</section>

<!-- Content page with image strip -->
<section class="page p-gallery">
  <div class="side-bar"></div>
  <h2 class="page-title" style="top:29px"><span class="l1">HEADING</span><span class="l2">GOES HERE</span></h2>
  <div class="brand-tab"><span class="mark"></span><span class="name">HARROWGATE<br>LABS</span></div>

  <h3 class="h-ink" style="left:17px;top:70px">HEADING GOES HERE</h3>
  <p class="copy" style="left:17px;top:84px;width:279px;height:70px">Lorem ipsum dolor sit amet, consectetuer adipiscing elit, sed diam nonummy nibh euismod tincidunt ut laoreet dolore magna aliquam erat volutpat. Ut wisi enim ad minim veniam, quis nostrud exerci tation ullamcorper suscipit lobortis nisl ut aliquip ex ea tation ullamcorper suscipit lobortis nisl ut aliquip ex ea commodo consequat. Duis autem vel eum iriure dolor in hendrerit in vulputate velit esse molestie consequat, vel illum dolore eu feugiat nulla facilisis at vero eros et accumsan et iusto odio dignis Lorem ipsum dolor sit amet, consectetuer adipiscing elit, sed diam nonummy nibh euismod tincidunt ut laoreet dolore magna aliquam erat volutpat. Ut wisi enim ad minim veniam, quis nostrud exerci tation ullamcorper suscipit lobortis nisl ut aliquip ex ea tation ullamcorper suscipit lobortis nisl ut aliquip ex ea commodo consequat. Duis autem vel eum iriure dolor in hendrerit in vulputate velit esse molestie consequat, vel illum dolore eu feugiat nulla facilisis at vero eros et accumsan et iusto odio dignis</p>
  <h3 class="h-ink" style="left:17px;top:160px">HEADING GOES HERE</h3>
  <p class="copy" style="left:17px;top:174px;width:279px;height:39px">Lorem ipsum dolor sit amet, consectetuer adipiscing elit, sed diam nonummy nibh euismod tincidunt ut laoreet dolore magna aliquam erat volutpat. Ut wisi enim ad minim veniam, quis nostrud exerci tation ullamcorper suscipit lobortis nisl ut aliquip ex ea tation ullamcorper suscipit lobortis nisl ut aliquip ex ea commodo consequat. Duis autem vel eum iriure dolor in hendrerit in vulputate velit esse molestie consequat, vel illum dolore eu feugiat nulla facilisis at vero eros et accumsan et iusto odio dignis Lorem ipsum dolor sit amet,</p>
  <h3 class="h-ink" style="left:17px;top:219px">HEADING GOES HERE</h3>
  <p class="copy" style="left:17px;top:234px;width:279px;height:39px">Lorem ipsum dolor sit amet, consectetuer adipiscing elit, sed diam nonummy nibh euismod tincidunt ut laoreet dolore magna aliquam erat volutpat. Ut wisi enim ad minim veniam, quis nostrud exerci tation ullamcorper suscipit lobortis nisl ut aliquip ex ea tation ullamcorper suscipit lobortis nisl ut aliquip ex ea commodo consequat. Duis autem vel eum iriure dolor in hendrerit in vulputate velit esse molestie consequat, vel illum dolore eu feugiat nulla facilisis at vero eros et accumsan et iusto odio dignis Lorem ipsum dolor sit amet,</p>
  <div class="photo" role="img" aria-label="Industrial equipment and pipework" style="left:17px;top:284px;width:70px;height:66px;background:linear-gradient(160deg,#4e6b7c,#a9c0c9 55%,#5e6e76)"></div>
  <div class="photo" role="img" aria-label="Factory production line" style="left:87px;top:284px;width:70px;height:66px;background:linear-gradient(160deg,#7b4a3a,#c79a7e 50%,#6d5248)"></div>
  <div class="photo" role="img" aria-label="Technician working on laboratory instruments" style="left:157px;top:284px;width:70px;height:66px;background:linear-gradient(160deg,#1f4f78,#4f8fb5 50%,#22405c)"></div>
  <div class="photo" role="img" aria-label="Clean stainless steel processing plant" style="left:227px;top:284px;width:69px;height:66px;background:linear-gradient(160deg,#b7cfe2,#eaf2f8 50%,#8fb1cc)"></div>
  <div class="footer"><span class="label">FACILITIES MANAGEMENT SERVICE</span><span class="num">PAGE - 01</span></div>
</section>

</body>
</html>
```